Healthy Meal Delivery Website needs a new face lift

Hi there,

The current website i have is super old and outdated.

I would like a beautiful modern site that has all the same content as the previous except with a a new, modern and trustworthy feel.

The current website is http://www.larkibite.ca/

Target Market(s)

Diet Meal delivery, weight loss, healthy meal delivery

Industry/Entity Type

Food Service

Number of Pages Required

5+ page

Font styles to use
Sans Serif

Requirements
Must have
• Modern & Clean
Should not have
• Anything outdated or cheesy

```html
<!DOCTYPE html>
<html lang="en">
<head>
<meta charset="utf-8">
<title>Larkibite Delivery — Fresh Diet Meals Delivered</title>
<link href="https://fonts.googleapis.com/css2?family=Open+Sans:wght@400;600;700&family=Pacifico&display=swap" rel="stylesheet">
<style>
:root{
  --blue:#2aa9dd;
  --ink:#222;
  --muted:#777;
  --line:#d9d9d9;
  --grey-band:#e8eaef;
  --navy:#101a32;
  --navy-deep:#0a1226;
  --icon:#1d2333;
  --footer-text:#8e97ad;
  --white:#fff;
}
*{box-sizing:border-box;margin:0;padding:0}
html,body{width:1200px;height:2835px;overflow:hidden}
body{font-family:"Open Sans",Arial,sans-serif;color:var(--ink);background:var(--white);position:relative}
.wrap{position:absolute;left:132px;width:936px}

/* header */
.site-header{position:absolute;top:0;left:0;width:1200px;height:113px;background:var(--white)}
.brand{position:absolute;left:132px;top:24px;display:flex;align-items:center;gap:10px}
.brand-dot{width:26px;height:26px;border-radius:50%;background:var(--blue)}
.brand-name{font-weight:700;font-size:28px;color:var(--blue);letter-spacing:.3px}
.contact-line{position:absolute;right:132px;top:20px;display:flex;gap:40px;font-size:16.5px;color:#333}
.contact-line span{display:flex;align-items:center;gap:8px}
.main-nav{position:absolute;right:132px;top:77px;display:flex;gap:24px;font-size:12.5px;color:#333}
.main-nav .active{color:var(--blue)}

/* hero */
.hero{position:absolute;top:113px;left:0;width:1200px;height:501px}
.hero-photo{position:absolute;inset:0;background:
  radial-gradient(ellipse 30% 40% at 45% 45%,#e27a52 0%,#d4643f 45%,rgba(212,100,63,0) 75%),
  radial-gradient(ellipse 40% 35% at 85% 30%,#6f9a3a 0%,rgba(111,154,58,0) 70%),
  radial-gradient(ellipse 30% 30% at 20% 70%,#7ea547 0%,rgba(126,165,71,0) 70%),
  radial-gradient(ellipse 80% 75% at 50% 40%,#f4f4f2 0%,#e6e7e6 60%,#cfcfcf 100%)}
.hero-band{position:absolute;left:0;bottom:0;width:1200px;height:85px;background:rgba(42,169,221,.92);text-align:center;color:var(--white)}
.hero-band h1{font-size:23px;font-weight:700;margin-top:16px;letter-spacing:.3px}
.hero-band p{font-size:16px;margin-top:2px}
.hero-arrow{position:absolute;width:30px;height:30px}

/* intro */
.intro{top:684px;text-align:center}
.section-title{font-size:33px;font-weight:700;color:var(--blue);text-align:center;letter-spacing:.3px}
.intro h3{font-size:26px;font-weight:400;color:#222;margin-top:4px}
.intro p{font-size:14.5px;line-height:26px;color:var(--muted);margin-top:14px}
.features{display:flex;justify-content:space-between;margin-top:28px;text-align:left}
.feature{width:150px}
.feature-icon{width:36px;height:36px;border-radius:50%;background:var(--icon);display:flex;align-items:center;justify-content:center}
.feature h4{font-size:12.5px;font-weight:700;margin-top:16px;color:#111}
.feature p{font-size:10.5px;line-height:15px;color:#444;margin-top:3px;max-width:128px}

/* program */
.program-band{position:absolute;top:1062px;left:0;width:1200px;height:601px;background:var(--grey-band)}
.program{top:1130px}
.cards{display:flex;justify-content:space-between;margin-top:22px}
.card{width:288px;height:380px;background:var(--white);box-shadow:0 1px 3px rgba(0,0,0,.12);position:relative}
.card-photo{height:172px}
.card h4{font-size:14px;font-weight:600;margin:16px 12px 0;color:#222}
.card p{font-size:10px;line-height:15px;color:#555;margin:8px 12px 0}
.btn{display:inline-block;background:var(--blue);color:var(--white);font-size:12px;font-weight:600;padding:9px 13px;letter-spacing:.2px}
.card .btn{position:absolute;left:12px;bottom:14px}

/* testimonials */
.testimonials{top:1730px;text-align:center}
.quote{font-size:17.5px;color:#333;margin-top:14px}
.quote-name{font-size:13px;color:#333;margin-top:6px}
.avatar{width:68px;height:68px;border-radius:50%;margin:12px auto 0;border:3px solid #333;background:radial-gradient(circle at 50% 45%,#c9a27a,#8a6a4d)}
.slider-arrow{position:absolute;top:1838px;width:24px;height:30px}
.divider{position:absolute;top:1986px;left:0;width:1200px;height:1px;background:#cfcfcf}

/* delivery */
.delivery{top:2055px}
.accordion{margin-top:12px;border-top:1px solid var(--line)}
.acc-item{border-bottom:1px solid var(--line);padding:14px 0 13px}
.acc-head{display:flex;align-items:center;gap:12px;font-size:15.5px;color:#222}
.acc-box{width:13px;height:13px;background:#222;position:relative}
.acc-box::before{content:"";position:absolute;left:3px;right:3px;top:5.5px;height:2px;background:var(--white)}
.acc-box.plus::after{content:"";position:absolute;top:3px;bottom:3px;left:5.5px;width:2px;background:var(--white)}
.acc-body{font-size:12px;color:#444;margin:6px 0 0 26px}
.delivery .center{text-align:center;margin-top:24px}

/* footer */
.site-footer{position:absolute;top:2461px;left:0;width:1200px;height:280px;background:var(--navy);color:var(--white)}
.footer-col{position:absolute;top:36px}
.footer-col h5{font-size:16px;font-weight:700;letter-spacing:.3px}
.about{left:132px;width:280px}
.about p{font-size:10px;line-height:16px;color:var(--footer-text);margin-top:10px}
.about .made{margin-top:16px}
.signoff{font-family:"Pacifico",cursive;font-size:18px;margin-top:4px;color:var(--white)}
.questions{left:466px;width:284px}
.field{background:var(--white);color:#333;font-size:11px;padding:10px 12px;height:34px}
.field-row{display:flex;justify-content:space-between;margin-top:16px}
.field-row .field{width:132px}
.field.msg{height:66px;margin-top:14px}
.submit{display:inline-block;background:var(--blue);font-size:11px;padding:9px 12px;margin-top:14px}
.contact{left:800px;width:300px}
.contact p{font-size:14px;color:#9aa3b8;margin-top:12px;line-height:22px;white-space:nowrap}
.contact .mail{color:var(--white);font-size:15px}
.contact .follow{margin-top:46px}
.socials{display:flex;gap:8px;margin-top:16px}
.socials span{width:25px;height:25px;border-radius:50%;background:var(--blue)}
.footer-bar{position:absolute;top:2741px;left:0;width:1200px;height:94px;background:var(--navy-deep);text-align:center;color:#9aa3b8;font-size:11px}
.footer-nav{margin-top:26px;display:flex;justify-content:center;gap:10px}
.footer-nav i{font-style:normal;color:#5d6680}
.copyright{margin-top:12px}
</style>
</head>
<body>

<header class="site-header">
  <div class="brand"><span class="brand-dot"></span><span class="brand-name">Larkibite Delivery</span></div>
  <div class="contact-line">
    <span><svg width="16" height="13" viewBox="0 0 16 13"><rect x="0" y="0" width="16" height="13" rx="1" fill="#333"/><path d="M1 1l7 6 7-6" stroke="#fff" stroke-width="1.4" fill="none"/></svg>E-mail:&nbsp; hello@larkibite.ca</span>
    <span><svg width="14" height="14" viewBox="0 0 24 24"><path d="M6.6 10.8a15 15 0 006.6 6.6l2.2-2.2a1 1 0 011-.25 11.4 11.4 0 003.6.57 1 1 0 011 1V20a1 1 0 01-1 1A17 17 0 013 4a1 1 0 011-1h3.5a1 1 0 011 1c0 1.25.2 2.45.57 3.57a1 1 0 01-.25 1z" fill="#333"/></svg>Call us on : 416-555-0192</span>
  </div>
  <nav class="main-nav">
    <span class="active">Home</span><span>How it Works</span><span>Pricing</span><span>Sample Menu</span><span>Celebrity</span><span>F.A.Q</span><span>Contact</span><span>Sign up</span><span>Customer Login</span>
  </nav>
</header>

<section class="hero">
  <div class="hero-photo" role="img" aria-label="Photo of a grilled salmon fillet with asparagus, arugula and cherry tomatoes on a white plate"></div>
  <div class="hero-band">
    <h1>FRESH DIET MEALS DELIVERED</h1>
    <p>Providing Toronto diet meal delivery for 15 years.</p>
    <svg class="hero-arrow" style="left:42px;top:28px" viewBox="0 0 30 30"><path d="M19 5L9 15l10 10" stroke="#fff" stroke-width="3.5" fill="none"/></svg>
    <svg class="hero-arrow" style="right:42px;top:28px" viewBox="0 0 30 30"><path d="M11 5l10 10-10 10" stroke="#fff" stroke-width="3.5" fill="none"/></svg>
  </div>
</section>

<section class="wrap intro">
  <h2 class="section-title">FRESH CUSTOMIZED DIET MEALS DELIVERED DAILY</h2>
  <h3>Toronto and Canada Wide</h3>
  <p>Fresh diet meal delivery Toronto and Canada wide is our signature fresh gourmet diet meal delivery program designed for healthy living &amp; weight loss management.Diet meal delivery Toronto has a creative gourmet menu that uses exotic flavors and ingredients to enhance your dining experience.</p>
  <div class="features">
    <div class="feature">
      <div class="feature-icon"><svg width="16" height="16" viewBox="0 0 16 16"><rect x="1.5" y="3" width="13" height="11.5" rx="1" fill="none" stroke="#fff" stroke-width="1.6"/><path d="M1.5 6.5h13M5 1v3M11 1v3" stroke="#fff" stroke-width="1.6"/></svg></div>
      <h4>BENEFITS</h4><p>Fresh diet meal delivery daily</p>
    </div>
    <div class="feature">
      <div class="feature-icon"><svg width="16" height="16" viewBox="0 0 16 16"><rect x="3" y="1.5" width="10" height="13" rx="1" fill="none" stroke="#fff" stroke-width="1.6"/><path d="M5.5 5h5M5.5 8h5" stroke="#fff" stroke-width="1.4"/></svg></div>
      <h4>MENU</h4><p>Inspired fresh gourmet Lark Diet meals</p>
    </div>
    <div class="feature">
      <div class="feature-icon"><svg width="16" height="16" viewBox="0 0 16 16"><rect x="5" y="1.5" width="9" height="10" fill="#fff"/><rect x="2" y="4.5" width="9" height="10" fill="#fff" stroke="#1d2333" stroke-width="1.2"/></svg></div>
      <h4>VARIETY</h4><p>60 Day Menu Rotation</p>
    </div>
    <div class="feature">
      <div class="feature-icon"><svg width="16" height="16" viewBox="0 0 16 16"><circle cx="8" cy="8" r="7" fill="#fff"/><path d="M4.8 8.2l2.2 2.2 4.2-4.4" stroke="#1d2333" stroke-width="1.8" fill="none"/></svg></div>
      <h4>CUSTOMIZATION</h4><p>Every fresh Lark Diet meal is personally customized</p>
    </div>
    <div class="feature">
      <div class="feature-icon"><svg width="17" height="14" viewBox="0 0 17 14"><rect x="0" y="1" width="10" height="9" fill="#fff"/><path d="M10 4h4l3 3v3h-7z" fill="#fff"/><circle cx="4" cy="11.5" r="2" fill="#fff" stroke="#1d2333"/><circle cx="13" cy="11.5" r="2" fill="#fff" stroke="#1d2333"/></svg></div>
      <h4>DELIVERY</h4><p>Fresh diet meal delivery daily Toronto and Canada wide</p>
    </div>
    <div class="feature">
      <div class="feature-icon"><svg width="16" height="16" viewBox="0 0 16 16"><path d="M2.5 10V8a5.5 5.5 0 0111 0v2" stroke="#fff" stroke-width="1.6" fill="none"/><rect x="1.5" y="9" width="3" height="5" rx="1" fill="#fff"/><rect x="11.5" y="9" width="3" height="5" rx="1" fill="#fff"/></svg></div>
      <h4>CUSTOMER SERVICE</h4><p>Personal Nutritionist available 7 days a week</p>
    </div>
  </div>
</section>

<div class="program-band"></div>
<section class="wrap program">
  <h2 class="section-title">PROGRAM DETAILS</h2>
  <div class="cards">
    <article class="card">
      <div class="card-photo" role="img" aria-label="Photo of a smiling woman in a white top in a bright kitchen" style="background:linear-gradient(100deg,#cfd8d4 0%,#e9ece8 45%,#f3f2ee 100%)"></div>
      <h4>CUSTOMIZED FOR YOU</h4>
      <p>The diet meal delivery program offers the widest selection of healthy options regarding your ingredients preference, allergies and special requests. We can also accommodate a Vegetarian and Gluten Free menu. Let us know what you need and we will do our best to accomodate your request.</p>
      <span class="btn">ORDER NOW</span>
    </article>
    <article class="card">
      <div class="card-photo" role="img" aria-label="Photo of a vegetable wrap cut in half" style="background:radial-gradient(ellipse at 50% 55%,#d8b27d 0%,#a86a3e 50%,#6a3b22 100%)"></div>
      <h4>PAUSE YOUR PROGRAM ANYTIME</h4>
      <p>You are welcome to pause and restart your meal program at anytime. Our customers lead busy lives, therefore if you need to post-pone a delivery let us know with at least 48 Hours notice prior to your delivery.</p>
      <span class="btn">ORDER NOW</span>
    </article>
    <article class="card">
      <div class="card-photo" role="img" aria-label="Photo of roasted chicken pieces with a golden glaze" style="background:radial-gradient(ellipse at 55% 50%,#e0782a 0%,#a83d14 55%,#4a180a 100%)"></div>
      <h4>ENJOY OUR GOURMET MENU</h4>
      <p>Every fresh diet meal delivered is prepared with the finest ingredients available and has a creative menu that uses unique and exotic flavors and ingredients to enhance your dining experience. Meals include Breakfast, Lunch, Dinner and 2 Snacks. You can view the fresh dining sample menu by clicking the link below.</p>
      <span class="btn">SAMPLE MENU HERE</span>
    </article>
  </div>
</section>

<section class="wrap testimonials">
  <h2 class="section-title">TESTIMONIALS</h2>
  <p class="quote">"The Lark Diet is simple and it works! I am so greatful to have used the Lark Diet. So tasty and so healthy."</p>
  <p class="quote-name">Marlow Keene - Actress</p>
  <div class="avatar" role="img" aria-label="Portrait photo of the reviewer"></div>
</section>
<svg class="slider-arrow" style="left:44px" viewBox="0 0 24 30"><path d="M16 4L6 15l10 11" stroke="#888" stroke-width="2" fill="none"/></svg>
<svg class="slider-arrow" style="right:44px" viewBox="0 0 24 30"><path d="M8 4l10 11-10 11" stroke="#888" stroke-width="2" fill="none"/></svg>
<div class="divider"></div>

<section class="wrap delivery">
  <h2 class="section-title">DELIVERY SYSTEM</h2>
  <div class="accordion">
    <div class="acc-item">
      <div class="acc-head"><span class="acc-box"></span>WHAT'S IN YOUR BAG?</div>
      <p class="acc-body">Your daily temperature controlled cooler will have all of your meals so you won't need to supplement with any additional snacks or produce during the day.</p>
    </div>
    <div class="acc-item"><div class="acc-head"><span class="acc-box plus"></span>YOUR DAILY MENU</div></div>
    <div class="acc-item"><div class="acc-head"><span class="acc-box plus"></span>RECYCLABLE CONTAINERS</div></div>
    <div class="acc-item"><div class="acc-head"><span class="acc-box plus"></span>RETURNING YOUR COOLER</div></div>
  </div>
  <div class="center"><span class="btn">ORDER NOW</span></div>
</section>

<footer class="site-footer">
  <div class="footer-col about">
    <h5>ABOUT US</h5>
    <p>The Lark Diet is based on 30% lean protein and the rest fruits and vegetables with a dash of Heart Healthy monounsaturated fats. Once these levels are reached and maintained, the body enters a state of hormonal balance which produces many positive effects, such as stable insulin and glucagon levels, increased energy, and weight loss.</p>
    <p class="made">Made with love by Larkibite.ca</p>
    <p class="signoff">The Larkibite Team</p>
  </div>
  <div class="footer-col questions">
    <h5>QUESTIONS?</h5>
    <div class="field-row"><div class="field">Name</div><div class="field">Email</div></div>
    <div class="field msg">Message</div>
    <span class="submit">SUBMIT</span>
  </div>
  <div class="footer-col contact">
    <h5>CONTACT US</h5>
    <p>Still have questions? Contact Us now at:<br><span class="mail">hello@larkibite.ca</span></p>
    <h5 class="follow">FOLLOW US ON</h5>
    <div class="socials"><span></span><span></span><span></span><span></span><span></span></div>
  </div>
</footer>
<div class="footer-bar">
  <div class="footer-nav"><span>Home</span><i>|</i><span>How it Works</span><i>|</i><span>Pricing</span><i>|</i><span>Sample Menu</span><i>|</i><span>Celebrity</span><i>|</i><span>F.A.Q</span><i>|</i><span>Contact</span><i>|</i><span>Sign up</span><i>|</i><span>Customer Login</span></div>
  <p class="copyright">Copyright © 2018 Larkibite. All rights reserved.</p>
</div>

</body>
</html>
```